Spring Detox sale graphics for social media

You MUST read the Brief in the WORD document and follow the instructions there. I want to create 10 social media graphics (new Instagram size 4:5 (1080 x 1350 pixels) focusing on our Mother’s Day Spring Detox Sale graphics, using any of the pics attached. Use the attached pics, NO RANDOM STOCK PHOTOGRAPHY. For the color scheme of the graphics, they should all be complementary to the product colors or feel like Spring time.

Target Market(s)

primarily women

Requirements
Must have
• the photos and text attached

```html
<!DOCTYPE html>
<html lang="en">
<head>
<meta charset="utf-8">
<title>Spring Detox Sale – Social Graphics</title>
<link href="https://fonts.googleapis.com/css2?family=Roboto:wght@400;500;700&display=swap" rel="stylesheet">
<style>
  :root {
    --board: #a8a8a8;
    --board-dark: #8e8e8e;
    --white: #ffffff;
    --ink: #333333;
    --coral: #e0463d;
    --maroon: #6b2222;
    --blush: #f8d7d6;
    --blush-faint: #fdf1f1;
    --wine: #4d1c22;
    --sale-red: #ea2a2f;
    --plum: #a0528a;
    --lilac: #a582ad;
    --lilac-light: #c9a6d3;
    --teal: #5b7b7b;
    --teal-light: #8fa9ad;
  }
  * { box-sizing: border-box; margin: 0; padding: 0; }
  html, body { width: 1100px; height: 1200px; overflow: hidden; }
  body {
    background: radial-gradient(ellipse at center, var(--board) 40%, var(--board-dark) 100%);
    font-family: "Roboto", Arial, sans-serif;
    position: relative;
  }
  .post {
    position: absolute;
    width: 392px;
    height: 490px;
    background: var(--white);
    overflow: hidden;
    box-shadow: 0 6px 22px rgba(0,0,0,0.28);
  }
  .post svg.bg { position: absolute; inset: 0; }
  .post--rings { left: 144px; top: 95px; }
  .post--supplements { left: 564px; top: 95px; }
  .post--everything { left: 144px; top: 615px; }
  .post--reset { left: 564px; top: 615px; }
  .text { position: absolute; font-weight: 700; white-space: nowrap; line-height: 1; }
  .photo { position: absolute; }

  /* post 1 */
  .post--rings .offer { left: 100px; top: 68px; width: 262px; text-align: center; font-size: 48px; color: var(--white); line-height: 65px; }
  .post--rings .headline { left: 110px; top: 163px; font-size: 40px; line-height: 53px; color: var(--ink); font-weight: 500; }
  .post--rings .headline .accent { color: var(--coral); font-weight: 400; }

  /* post 2 */
  .post--supplements .offer { left: 0; width: 392px; top: 16px; text-align: center; font-size: 63px; color: var(--white); }
  .post--supplements .title { left: 0; width: 392px; top: 126px; text-align: center; font-size: 50px; line-height: 52px; color: var(--maroon); }
  .post--supplements .subtitle { left: 0; width: 392px; top: 234px; text-align: center; font-size: 32px; color: var(--sale-red); }
  .post--supplements .photo { left: 18px; top: 283px; width: 374px; height: 207px;
    background: linear-gradient(180deg, #f2f0ef 0%, #ebe7e6 55%, #f3453f 100%); }

  /* post 3 */
  .post--everything .band-title { left: 0; width: 392px; top: 9px; text-align: center; font-size: 42px; color: var(--white); font-weight: 500; }
  .post--everything .line { left: 36px; font-size: 48px; color: var(--ink); }
  .post--everything .line--1 { top: 86px; }
  .post--everything .line--2 { top: 150px; color: var(--plum); font-weight: 500; }
  .post--everything .line--3 { top: 210px; color: var(--white); font-size: 54px; }
  .post--everything .line--4 { top: 282px; }

  /* post 4 */
  .post--reset .offer { left: 25px; top: 14px; font-size: 61px; color: var(--white); font-weight: 500; }
  .post--reset .title { left: 25px; top: 100px; font-size: 40px; line-height: 46px; color: var(--ink); }
  .post--reset .title .accent { color: var(--teal); }
  .post--reset .tagline { left: 26px; top: 250px; font-size: 23px; line-height: 28px; color: var(--ink); font-weight: 400; }
  .post--reset .photo { left: 108px; top: 85px; width: 284px; height: 405px;
    background: linear-gradient(180deg, #eae6e3 0%, #dcd6d2 55%, #f3f2f2 78%, #e6e4e8 100%); border-radius: 40px 0 0 0; }
</style>
</head>
<body>

<!-- Post 1: rings -->
<section class="post post--rings">
  <svg class="bg" width="392" height="490" viewBox="0 0 392 490">
    <circle cx="195" cy="196" r="185" fill="none" stroke="var(--blush-faint)" stroke-width="28"/>
    <circle cx="195" cy="196" r="130" fill="none" stroke="#f5eeee" stroke-width="22"/>
    <circle cx="14" cy="101" r="104" fill="var(--coral)"/>
    <circle cx="14" cy="101" r="84" fill="var(--white)"/>
    <circle cx="14" cy="101" r="77" fill="var(--maroon)"/>
    <circle cx="14" cy="101" r="66" fill="var(--white)"/>
    <path d="M100 68 H362 Q378 100 362 133 H100 Z" fill="var(--coral)"/>
    <path d="M362 68 Q380 100 362 133 H358 Q374 100 358 68 Z" fill="var(--maroon)"/>
    <circle cx="73" cy="455" r="92" fill="#fbe8e8"/>
    <circle cx="73" cy="455" r="72" fill="#e6d5d6"/>
    <circle cx="73" cy="455" r="64" fill="var(--white)"/>
    <circle cx="73" cy="455" r="56" fill="var(--blush)"/>
    <circle cx="392" cy="440" r="122" fill="var(--coral)"/>
    <circle cx="392" cy="440" r="103" fill="var(--white)"/>
    <circle cx="392" cy="440" r="84" fill="var(--maroon)"/>
    <circle cx="392" cy="440" r="72" fill="var(--white)"/>
    <circle cx="392" cy="440" r="61" fill="var(--coral)"/>
  </svg>
  <div class="text offer">25% OFF</div>
  <div class="text headline">Mother’s Day<br><span class="accent">Spring Detox</span><br>Sale.</div>
</section>

<!-- Post 2: all supplements -->
<section class="post post--supplements">
  <svg class="bg" width="392" height="490" viewBox="0 0 392 490">
    <defs>
      <linearGradient id="wineGrad" x1="0" y1="0" x2="1" y2="0">
        <stop offset="0" stop-color="#5a1a1a"/><stop offset="1" stop-color="#4a1f2c"/>
      </linearGradient>
    </defs>
    <path d="M0 0 H392 V100 C300 80 220 92 160 112 C100 128 40 124 0 108 Z" fill="url(#wineGrad)"/>
    <path d="M0 108 C40 124 100 128 160 112 C220 92 300 80 392 100 V106 C300 88 220 100 160 120 C100 136 40 132 0 116 Z" fill="var(--sale-red)"/>
    <path d="M0 490 V392 C120 420 260 370 392 360 V490 Z" fill="var(--sale-red)"/>
  </svg>
  <div class="text offer">25% OFF</div>
  <div class="text title">All<br>Supplements</div>
  <div class="text subtitle">Spring Detox Sale!</div>
  <div class="photo" role="img" aria-label="Product photo: four white supplement bottles in a row"></div>
</section>

<!-- Post 3: everything -->
<section class="post post--everything">
  <svg class="bg" width="392" height="490" viewBox="0 0 392 490">
    <defs>
      <linearGradient id="lilacGrad" x1="0" y1="0" x2="1" y2="1">
        <stop offset="0" stop-color="var(--lilac)"/><stop offset="1" stop-color="var(--lilac-light)"/>
      </linearGradient>
    </defs>
    <rect x="0" y="0" width="392" height="61" fill="var(--plum)"/>
    <rect x="0" y="203" width="309" height="64" fill="var(--lilac)"/>
    <rect x="299" y="203" width="10" height="64" fill="var(--plum)"/>
    <path d="M0 405 C100 440 170 410 240 385 C300 368 340 380 392 395 V490 H0 Z" fill="url(#lilacGrad)"/>
    <path d="M20 412 C110 440 170 410 240 383 C290 364 330 368 370 378 C330 362 290 362 240 378 C170 404 110 434 20 412 Z" fill="var(--plum)"/>
  </svg>
  <div class="text band-title">MOTHER’S DAY</div>
  <div class="text line line--1">Spring</div>
  <div class="text line line--2">Detox Sale:</div>
  <div class="text line line--3">25% OFF</div>
  <div class="text line line--4">Everything!</div>
</section>

<!-- Post 4: spring reset -->
<section class="post post--reset">
  <svg class="bg" width="392" height="490" viewBox="0 0 392 490">
    <circle cx="240" cy="195" r="150" fill="none" stroke="#f1f2f2" stroke-width="30"/>
    <circle cx="198" cy="500" r="186" fill="none" stroke="var(--teal)" stroke-width="22"/>
    <circle cx="198" cy="500" r="152" fill="none" stroke="var(--teal-light)" stroke-width="16"/>
    <path d="M0 0 H348 Q370 42 348 85 H0 Z" fill="var(--teal)"/>
    <path d="M358 0 Q380 42 358 85 H352 Q372 42 352 0 Z" fill="var(--teal-light)"/>
  </svg>
  <div class="photo" role="img" aria-label="Photo: smiling woman in a white cropped sweater behind a row of supplement bottles"></div>
  <div class="text offer">25% OFF</div>
  <div class="text title"><span class="accent">Spring</span><br>Detox<br><span class="accent">Sale:</span></div>
  <div class="text tagline">Spring Reset.<br>Summer<br>Ready</div>
</section>

</body>
</html>
```